Professional Services - letterhead / business cards

The company (velmora partners) will provide services to Investment Funds and large investors in Spain. I have recently chosen a logo that I am attaching.

I would like a simple stationary design that i could use as letter head, business cards and "with compliments" cards.

I am not quite sure which color I will mostly use for the logo, in the email signature I will probably lean towards the white background and grey letters. I am attaching my favourite options.

Target Market(s)

Large Multinationals, Investment funds and Law firms

Industry/Entity Type

Business

Requirements
Must have
• my details are:
Luis R. Abadal
Velmora Partners S.L.
Casa de Torrelumbre
Calle de Vientoalto 27
28014 Madrid
T: +34 (91) 387-2265
M: +34 (646) 819-054
e-mail: labadal@velmorapartners.com

```html
<!DOCTYPE html>
<html lang="en">
<head>
<meta charset="utf-8">
<title>Velmora Partners – Business Cards</title>
<link rel="stylesheet" href="https://fonts.googleapis.com/css2?family=Jost:wght@300;400;500;700&display=swap">
<style>
  :root {
    --navy: #262a5c;
    --band-grey: #a7a8ab;
    --text-grey: #5b5c60;
    --divider-grey: #c9cacc;
    --card-white: #ffffff;
    --backdrop: #ebe8e4;
  }
  * { margin: 0; padding: 0; box-sizing: border-box; }
  html, body {
    width: 1200px; height: 719px; overflow: hidden;
    background: var(--backdrop);
    font-family: "Jost", sans-serif;
  }
  .stage { position: relative; width: 1200px; height: 719px; }

  .card {
    position: absolute;
    width: 540px; height: 342px;
    background: var(--card-white);
    border-radius: 24px;
    box-shadow: 0 10px 28px rgba(0,0,0,.18);
    overflow: hidden;
  }
  .card--front { left: 70px; top: 90px; z-index: 2; }
  .card--back  { left: 600px; top: 290px; z-index: 1; }

  .wordmark {
    color: var(--navy);
    font-weight: 300;
    font-size: 48px;
    letter-spacing: .5px;
    white-space: nowrap;
  }
  .card--front .wordmark { position: absolute; left: 56px; top: 62px; }

  .contact-band {
    position: absolute; left: 0; right: 0; top: 168px; height: 100px;
    background: var(--band-grey);
    border-top: 2px solid var(--navy);
    display: flex; align-items: center;
  }
  .address {
    width: 250px; text-align: right;
    padding-right: 18px;
    color: #3c3d41; font-size: 15px; line-height: 1.3;
  }
  .band-divider { width: 1px; height: 68px; background: #e4e4e6; }
  .contacts { list-style: none; padding-left: 16px; color: #1c1d22; font-size: 14.5px; line-height: 1.45; }
  .contacts li { display: flex; align-items: center; gap: 8px; }
  .contacts svg { width: 12px; height: 12px; flex: none; }

  .signature-rule {
    position: absolute; left: 0; right: 0; top: 280px;
    height: 1px; background: var(--navy);
  }
  .signature {
    position: absolute; right: 38px; top: 292px;
    font-size: 20px; white-space: nowrap;
  }
  .signature .person { color: var(--navy); font-weight: 700; letter-spacing: 1.5px; }
  .signature .company { color: var(--text-grey); font-weight: 300; font-size: 14px; }

  .card--back .wordmark {
    position: absolute; left: 0; right: 0; top: 100px; text-align: center;
  }
  .website {
    position: absolute; left: 0; right: 0; top: 252px; text-align: center;
    color: var(--navy); font-weight: 500; font-size: 14px; letter-spacing: 7px;
  }
</style>
</head>
<body>
<main class="stage">

  <section class="card card--front" aria-label="Business card front">
    <div class="wordmark">velmora partners</div>

    <div class="contact-band">
      <address class="address" style="font-style:normal">
        Casa de Torrelumbre<br>
        Calle de Vientoalto 27<br>
        28014 Madrid
      </address>
      <div class="band-divider"></div>
      <ul class="contacts">
        <li>
          <svg viewBox="0 0 12 12" aria-hidden="true"><circle cx="6" cy="6" r="5.3" fill="none" stroke="#1c1d22" stroke-width="1"/><path d="M4 3.3 L5 3.1 L5.4 4.6 L4.8 5.1 Q5.4 6.6 6.9 7.2 L7.4 6.6 L8.9 7 L8.7 8 Q6.8 8.8 4.8 7.1 Q3.3 5.4 4 3.3Z" fill="#1c1d22"/></svg>
          +34 (91) 387-2265
        </li>
        <li>
          <svg viewBox="0 0 12 12" aria-hidden="true"><rect x="3.5" y="1" width="5" height="10" rx="1" fill="#1c1d22"/><rect x="4.3" y="2.2" width="3.4" height="4.5" fill="#a7a8ab"/></svg>
          +34 (646) 819-054
        </li>
        <li>
          <svg viewBox="0 0 12 12" aria-hidden="true"><rect x="1" y="3" width="10" height="7" fill="#1c1d22"/><path d="M1 3 L6 7 L11 3" fill="none" stroke="#a7a8ab" stroke-width="1"/></svg>
          labadal@velmorapartners.com
        </li>
      </ul>
    </div>

    <div class="signature-rule"></div>
    <p class="signature"><span class="person">LUIS R. ABADAL,</span> <span class="company">Velmora Partners S.L.</span></p>
  </section>

  <section class="card card--back" aria-label="Business card back">
    <div class="wordmark">velmora partners</div>
    <p class="website">www.velmorapartners.com</p>
  </section>

</main>
</body>
</html>
```